Velmora Consulting Business

** Please add the content information from my old business card
1. I would like to see a two sided business card with both options with the 1st Option--Tallow Spire-new WHITE BACKGROUND LOGO
2 nd Option-Tallow Spire - new BLACK- Background Logo
3rd -Option a business card with my Photo on the card
Please add the new word to the card information:
EXECUTION
AS THE OWNER'S REP
WE AIM TO ACHIEVE YOUR
INFRASTRUCTURE VISION with
OUR SPECIALIZATION & EXECUTION in:

FUNDING Planning
BUSINESS Planning
INFRASTRUCTURE Planning
PROJECT Management
Since 2012
_____________________________________________________________________
I want to get spot uv raised printing. I was liking a a nice rich white linen paper stock with black writing & NOT A COLORED CARD other than a variety of white or black cards concept

```html
<!DOCTYPE html>
<html lang="en">
<head>
<meta charset="utf-8">
<title>Velmora Consulting – Business Card</title>
<link rel="stylesheet" href="https://fonts.googleapis.com/css2?family=Source+Sans+3:wght@400;600&display=swap">
<style>
  :root {
    --backdrop: #9b9b9b;
    --paper-white: #f1f1f1;
    --paper-black: #1c1c1c;
    --ink: #1a1a1a;
    --ink-soft: #2e2e2e;
    --ink-light: #f4f4f4;
    --accent-red: #e0223f;
    --mark-faint: #353535;
  }
  * { box-sizing: border-box; margin: 0; padding: 0; }
  html, body {
    width: 1093px;
    height: 1200px;
    overflow: hidden;
    background: var(--backdrop);
    font-family: "Source Sans 3", "Myriad Pro", sans-serif;
  }
  .canvas { position: relative; width: 1093px; height: 1200px; }

  .card {
    position: absolute;
    left: 264px;
    width: 578px;
    height: 357px;
    border-radius: 24px;
    overflow: hidden;
  }
  .card--front { top: 226px; background: var(--paper-white); color: var(--ink); }
  .card--back  { top: 621px; background: var(--paper-black); color: var(--ink-light); }

  /* Front */
  .holder-name {
    position: absolute; left: 27px; top: 50px;
    font-size: 21px; font-weight: 600; letter-spacing: 0.1px;
  }
  .holder-role {
    position: absolute; left: 27px; top: 76px;
    font-size: 14.5px; color: var(--accent-red);
  }
  .brand-name {
    position: absolute;
    font-weight: 600;
    white-space: nowrap;
    transform: translateX(-50%);
    text-align: center;
  }
  .card--front .brand-name {
    left: 442px; top: 132px;
    font-size: 36px; line-height: 1.05; color: var(--ink);
  }
  .contact-list {
    position: absolute; left: 27px; top: 263px;
    list-style: none;
  }
  .contact-item {
    display: flex; align-items: center;
    height: 21px;
    font-size: 16px;
  }
  .contact-icon { width: 16px; height: 16px; margin-right: 9px; fill: var(--ink); }
  .office-locations {
    position: absolute; right: 28px; top: 306px;
    font-size: 16px;
  }
  .office-sep { color: var(--accent-red); margin: 0 3px; }

  /* Back */
  .card--back .brand-name {
    left: 439px; top: 135px;
    font-size: 36px; line-height: 1.05; color: var(--mark-faint);
  }
  .mission {
    position: absolute; left: 31px; top: 131px;
    font-size: 13.5px; line-height: 18.4px; text-transform: none;
  }
  .services {
    position: absolute; left: 31px; top: 263px;
    display: grid; grid-template-columns: 207px auto;
    row-gap: 2px;
    list-style: none;
    font-size: 14px;
  }
  .service { display: flex; align-items: center; height: 17px; }
  .service-bullet {
    width: 8px; height: 8px; border-radius: 50%;
    background: var(--accent-red); margin-right: 10px;
  }
  .rule {
    position: absolute; left: 31px; top: 305px;
    width: 510px; height: 1px; background: var(--ink-light);
  }
  .since {
    position: absolute; right: 37px; top: 312px;
    font-size: 14px;
  }
</style>
</head>
<body>
<main class="canvas">

  <section class="card card--front" aria-label="Business card, front">
    <h1 class="holder-name">Marisol Avendale-Crane</h1>
    <p class="holder-role">CEO / LEAD PROJECT MANAGER</p>

    <p class="brand-name">Velmora<br>Consulting</p>

    <ul class="contact-list">
      <li class="contact-item">
        <svg class="contact-icon" viewBox="0 0 24 24" aria-hidden="true"><path d="M6.6 10.8a15.1 15.1 0 0 0 6.6 6.6l2.2-2.2a1 1 0 0 1 1-.25 11.4 11.4 0 0 0 3.6.57 1 1 0 0 1 1 1V20a1 1 0 0 1-1 1A17 17 0 0 1 3 4a1 1 0 0 1 1-1h3.5a1 1 0 0 1 1 1c0 1.25.2 2.45.57 3.57a1 1 0 0 1-.25 1z"/></svg>
        555.010.2748
      </li>
      <li class="contact-item">
        <svg class="contact-icon" viewBox="0 0 24 24" aria-hidden="true"><path d="M2 5h20v14H2zM3.5 6.5 12 13l8.5-6.5z" fill-rule="evenodd"/></svg>
        mari@velmora.ca
      </li>
      <li class="contact-item">
        <svg class="contact-icon" viewBox="0 0 24 24" aria-hidden="true"><path d="M12 2a10 10 0 1 0 0 20 10 10 0 0 0 0-20zm0 2c.9 0 2.2 2 2.7 5H9.3C9.8 6 11.1 4 12 4zM4.3 11h3a17 17 0 0 0 0 2h-3a8 8 0 0 1 0-2zm5 0h5.4a15 15 0 0 1 0 2H9.3a15 15 0 0 1 0-2zm7.4 0h3a8 8 0 0 1 0 2h-3a17 17 0 0 0 0-2zM9.3 15h5.4c-.5 3-1.8 5-2.7 5s-2.2-2-2.7-5zM5 9a8 8 0 0 1 4-4.3A13 13 0 0 0 7.5 9zm11.5 0A13 13 0 0 0 15 4.7 8 8 0 0 1 19 9zM5 15h2.5A13 13 0 0 0 9 19.3 8 8 0 0 1 5 15zm11.5 0H19a8 8 0 0 1-4 4.3 13 13 0 0 0 1.5-4.3z"/></svg>
        www.velmora.ca
      </li>
    </ul>

    <p class="office-locations">Northvale NT<span class="office-sep">•</span>Ashbury NB</p>
  </section>

  <section class="card card--back" aria-label="Business card, back">
    <p class="brand-name">Velmora<br>Consulting</p>

    <p class="mission">
      EXECUTION<br>
      AS THE OWNER'S REP<br>
      WE AIM TO ACHIEVE YOUR<br>
      INFRASTRUCTURE VISION with<br>
      OUR SPECIALIZATION &amp; EXECUTION in:
    </p>

    <ul class="services">
      <li class="service"><span class="service-bullet"></span>FUNDING Planning</li>
      <li class="service"><span class="service-bullet"></span>BUSINESS Planning</li>
      <li class="service"><span class="service-bullet"></span>INFRASTRUCTURE Planning</li>
      <li class="service"><span class="service-bullet"></span>PROJECT Management</li>
    </ul>

    <div class="rule"></div>
    <p class="since">Since 2012</p>
  </section>

</main>
</body>
</html>
```